Business card for Crestline Bathrooms

Please design a business card for our bathroom renovation business. You can use my existing logo, but if you have an idea to modernize it, I would like to see it. Please see attached files first. I would like to use the blue and the orange theme. I like the concept of using the shower head in the logo. Please find following a design (or two) that I have been trying to create with my limited resources. That design was for a sign, but I was going to adopt it and use it as a business card as well. I like the concept of the water splash but I don’t think it “flows” nicely together with the logo. Another thought is that maybe creating the logo out of water splash could work and have a dramatic effect (like the water text and the butterfly picture attached with similar background instead of white). If the above doesn’t work I would like to see a modern simplified design. One of the attached files named as the unwanted business card has all the details that I want included in the business card. Please note that it is two sided.
Updates

I am very thankful for the designs that I have received, but they are very similar and only a couple of attempts to do something with the water splash as per my original brief. Modernizing the logo and having it made out of out of water splash with the orange as color accent could work and have a dramatic effect (like the water text and the butterfly picture attached with similar background instead of white). Please do not use the butterfly itself! This is just an example that images can be created out of water splash.

Contact Information for Business Card

all the details are on the unwonted business card file included

Colors
3176b5

Requirements
Nice to have
• Copied from the brief:
• ... maybe creating the logo out of water splash could work and have a dramatic effect (like the water text and the butterfly picture attached with similar background instead of white). Please do not use the butterfly itself!
Should not have
• I am getting designs with a butterfly. The butterfly picture was an example of creating something from a water splash. The butterfly itself has no association with anything other than the concept of creating a logo out of water splash. Sorry, I thought I was clear in the brief.

```html
<!DOCTYPE html>
<html lang="en">
<head>
<meta charset="utf-8">
<title>Crestline Bathrooms – Business Card</title>
<link href="https://fonts.googleapis.com/css2?family=Roboto+Condensed:wght@400;700&display=swap" rel="stylesheet">
<style>
  :root {
    --page: #e9ecef;
    --card-black: #161718;
    --card-blue: #3176b5;
    --blue-light: #9cc3e6;
    --blue-deep: #1f5a92;
    --splash-top: #c9d3da;
    --splash-mid: #8fa6b8;
    --splash-low: #5f7d96;
    --text-light: #e8eef3;
    --shadow: rgba(0, 0, 0, 0.18);
  }
  * { box-sizing: border-box; margin: 0; padding: 0; }
  html, body { width: 1200px; height: 800px; overflow: hidden; }
  body {
    background: var(--page);
    font-family: "Roboto Condensed", Arial, sans-serif;
    display: flex;
    align-items: center;
    justify-content: center;
    gap: 90px;
  }
  .card {
    width: 330px;
    height: 576px;
    border-radius: 14px;
    overflow: hidden;
    position: relative;
    box-shadow: 0 10px 28px var(--shadow);
  }

  /* Front */
  .card--front { background: var(--card-black); display: flex; }
  .front__splash {
    width: 42%;
    height: 100%;
    background: linear-gradient(160deg, var(--splash-top) 0%, var(--splash-mid) 55%, var(--splash-low) 100%);
    border-right: 3px solid var(--blue-light);
  }
  .front__details {
    flex: 1;
    padding: 34px 22px 30px 22px;
    display: flex;
    flex-direction: column;
    color: var(--text-light);
  }
  .brand-name {
    font-size: 19px;
    font-weight: 400;
    color: var(--text-light);
    letter-spacing: 0.5px;
    line-height: 1.15;
    display: flex;
    align-items: center;
    gap: 8px;
  }
  .brand-name__dot {
    width: 10px; height: 10px; border-radius: 50%;
    background: var(--blue-light);
    flex: none;
  }
  .person-name {
    margin-top: 46px;
    font-size: 24px;
    font-weight: 700;
    color: var(--blue-light);
    text-transform: uppercase;
    letter-spacing: 0.5px;
    line-height: 1.05;
  }
  .person-name__rule {
    margin-top: 12px;
    width: 100%;
    height: 3px;
    background: var(--blue-light);
  }
  .contact-list { list-style: none; margin-top: 28px; display: flex; flex-direction: column; gap: 18px; }
  .contact-item { display: flex; align-items: flex-start; gap: 10px; font-size: 15px; line-height: 1.3; }
  .contact-item__badge {
    width: 20px; height: 20px; flex: none;
    border-radius: 50%;
    background: var(--text-light);
    color: var(--card-black);
    font-size: 11px; font-weight: 700;
    display: flex; align-items: center; justify-content: center;
  }
  .contact-item__text { word-break: break-all; }
  .contact-item__text--web { font-size: 13.5px; }

  /* Back */
  .card--back {
    background: linear-gradient(200deg, #3f86c6 0%, var(--card-blue) 55%, var(--blue-deep) 100%);
    color: var(--text-light);
  }
  .back__splash {
    position: absolute; left: 0; top: 0;
    width: 46%; height: 44%;
    background: radial-gradient(ellipse at 30% 30%, rgba(220,232,242,0.55) 0%, rgba(160,190,215,0.25) 50%, rgba(49,118,181,0) 80%);
  }
  .back__services {
    position: absolute; top: 34px; right: 28px;
    list-style: none;
    font-size: 14px; font-weight: 700;
    text-transform: uppercase; letter-spacing: 0.5px;
    display: flex; flex-direction: column; gap: 8px;
  }
  .back__rules { position: absolute; top: 150px; right: 28px; display: flex; flex-direction: column; gap: 6px; }
  .back__rules span { display: block; width: 150px; height: 3px; background: var(--card-black); }
  .back__brand {
    position: absolute; left: 0; right: 0; bottom: 150px;
    text-align: center;
    font-size: 30px; font-weight: 400;
    color: rgba(232, 238, 243, 0.35);
    letter-spacing: 1px;
  }
</style>
</head>
<body>
  <article class="card card--front">
    <div class="front__splash" role="img" aria-label="Photograph of a water splash in silvery blue tones"></div>
    <div class="front__details">
      <div class="brand-name"><span class="brand-name__dot"></span>Crestline Bathrooms</div>
      <h1 class="person-name">Daniel Moretti</h1>
      <div class="person-name__rule"></div>
      <ul class="contact-list">
        <li class="contact-item"><span class="contact-item__badge">A</span><span class="contact-item__text">PO Box 41<br>Kellerton 2708</span></li>
        <li class="contact-item"><span class="contact-item__badge">P</span><span class="contact-item__text">0400 555 218<br>6200 5147</span></li>
        <li class="contact-item"><span class="contact-item__badge">W</span><span class="contact-item__text contact-item__text--web">daniel@crestlinebathrooms.com.au<br>crestlinebathrooms.com.au</span></li>
      </ul>
    </div>
  </article>

  <article class="card card--back">
    <div class="back__splash" role="img" aria-label="Faint water splash photograph over the blue background"></div>
    <ul class="back__services">
      <li>• Full Renovations</li>
      <li>• Waterproofing</li>
      <li>• Tiling &amp; Fixtures</li>
    </ul>
    <div class="back__rules"><span></span><span></span></div>
    <div class="back__brand">Crestline Bathrooms</div>
  </article>
</body>
</html>
```